Tour operator needs simple coded WordPress site (updated extra payment for coding and guaranteed)

[update 9/7/2015]
If you design a new logo and it gets accepted, even if we use another template with your logo you will get $50
[update 8/7/2015]
Update on questions about dual-language
For dual languages we are happy to set up a second site with the same designs in a second language.
For the design aspect just allow the user to switch between languages with an icon.
For the coding, a replica of the site on a second server will do (to save messing around with multiple language plugins) - we will populate it with Chinese text
[original post]
Simple coded WordPress site for tours
You can choose to design only or design and code ($340 design, $150 bonus for coding)
Open design brief - use your creativity
Will be in 2 languages (English and Chinese) but design needs only to be in one language
Winning design will be chosen only from home page, but the winner must make a second standard template page when chosen at no extra cost.
Must be responsive design
We only need homepage and standard template page design and coding, we will populate the pages
You can use design ideas from our pamphlet if you like - attached
Only a sample logo and colors on website and pamphlet - feel free to change as the current ones seem restrictive
Current website framework only to give an idea of the number of pages and basic menu structure (no need to use existing navigation style or any style at all for that matter, open brief)
http://brightwattlejourneys.com.au/
Target Market(s)
Chinese parents of kids 10-14 (the kids will take the tour)
Industry/Entity Type
Tour
Number of Pages Required
2 page
Look and feel
Each slider illustrates characteristics of the customer's brand and the style your logo design should communicate.

```html
<!DOCTYPE html>
<html lang="en">
<head>
<meta charset="utf-8">
<title>Bright Wattle Journeys</title>
<link href="https://fonts.googleapis.com/css2?family=Ubuntu:wght@400;500&family=Oxygen:wght@300;400;700&family=Oregano&display=swap" rel="stylesheet">
<style>
:root{
  --navy:#2f3f85;
  --navy-line:#4a5a9c;
  --gold:#f5b31b;
  --ink:#2a2a2a;
  --text:#333;
  --dark-btn:#2b2b2b;
  --white:#fff;
  --soft:#ececec;
}
*{margin:0;padding:0;box-sizing:border-box}
html,body{width:1200px;height:1147px;overflow:hidden;background:var(--white)}
body{position:relative;font-family:"Oxygen",Arial,sans-serif;color:var(--text)}
.site-header{position:absolute;left:0;top:0;width:1200px;height:96px;background:var(--white)}
.brand{position:absolute;left:176px;top:12px;width:174px;height:174px;border-radius:50%;background:var(--white);border:4px solid var(--navy);z-index:5;display:flex;align-items:center;justify-content:center;text-align:center}
.brand-name{font-family:"Ubuntu",sans-serif;font-weight:500;font-size:20px;line-height:24px;color:var(--navy);text-transform:uppercase;width:130px}
.lang-switch{position:absolute;left:815px;top:22px;width:118px;height:32px;background:var(--dark-btn);border-radius:3px;color:var(--white);font-family:"Ubuntu",sans-serif;font-size:13px;display:flex;align-items:center;padding-left:18px;gap:8px}
.lang-flag{width:20px;height:13px;background:linear-gradient(135deg,#2b3f86,#c8202f 50%,#2b3f86)}
.btn-book{position:absolute;left:950px;top:21px;width:89px;height:33px;background:var(--gold);border-radius:2px;color:var(--white);font-family:"Ubuntu",sans-serif;font-weight:500;font-size:14px;display:flex;align-items:center;justify-content:center}
.main-nav{position:absolute;left:0;top:96px;width:1200px;height:42px;background:var(--navy)}
.main-nav ul{list-style:none;position:absolute;left:414px;top:0;display:flex;height:42px;border-left:1px solid var(--navy-line)}
.main-nav li{height:42px;display:flex;align-items:center;justify-content:center;border-right:1px solid var(--navy-line);color:var(--white);font-family:"Ubuntu",sans-serif;font-weight:500;font-size:15px}
.main-nav li.is-current{box-shadow:inset 0 -3px 0 var(--gold)}
.hero{position:absolute;left:0;top:138px;width:1200px;height:419px}
.hero-photo{position:absolute;inset:0;background:linear-gradient(180deg,#b9c8d6 0%,#8aa0b4 30%,#7c6d66 60%,#5b3f3a 100%)}
.hero-arrow{position:absolute;top:206px;width:20px;height:30px}
.hero-caption{position:absolute;left:0;bottom:0;width:1200px;height:54px;background:rgba(40,36,36,.82);color:var(--white);font-family:"Oregano",cursive;font-size:26px;display:flex;align-items:center;justify-content:center;letter-spacing:.2px}
.features{position:absolute;left:0;top:590px;width:1200px}
.feature{position:absolute;width:240px;text-align:center}
.feature-ring{width:132px;height:132px;margin:0 auto;border-radius:50%;border:2px solid var(--gold);padding:6px}
.feature-ring.navy{border-color:var(--navy)}
.feature-photo{width:100%;height:100%;border-radius:50%}
.feature-title{margin-top:18px;font-family:"Ubuntu",sans-serif;font-weight:500;font-size:16px;color:var(--ink)}
.feature-title.navy{color:var(--navy)}
.lower{position:absolute;left:0;top:797px;width:1200px;height:309px;background:linear-gradient(180deg,#fff 0%,#fff 45%,var(--soft) 100%)}
.rule{position:absolute;left:160px;top:0;width:882px;height:2px;background:#dcdcdc}
.about-title{position:absolute;left:0;top:34px;width:1200px;text-align:center;font-family:"Ubuntu",sans-serif;font-weight:500;font-size:27px;color:var(--navy)}
.about-title .gold{color:var(--gold)}
.title-ornament{position:absolute;left:280px;top:70px;width:640px;height:18px}
.about-lead{position:absolute;left:170px;top:104px;width:860px;text-align:center;font-weight:700;font-size:13px;line-height:19px;color:var(--ink)}
.about-body{position:absolute;left:170px;top:187px;width:860px;text-align:center;font-weight:300;font-size:13px;line-height:19px;color:var(--ink)}
.btn-more{position:absolute;left:548px;top:242px;width:105px;height:32px;background:#333;border:1px solid #222;border-radius:3px;color:var(--white);font-family:"Ubuntu",sans-serif;font-size:13px;display:flex;align-items:center;justify-content:center}
.site-footer{position:absolute;left:0;top:1106px;width:1200px;height:41px;background:var(--navy);color:var(--white);font-size:13px}
.copyright{position:absolute;left:161px;top:12px}
.social{position:absolute;left:907px;top:0;display:flex;gap:7px}
.social span{width:39px;height:39px;border-radius:50%;background:var(--white);border:3px solid #d8dbe6}
</style>
</head>
<body>
<header class="site-header">
  <div class="brand"><span class="brand-name">Bright Wattle Journeys</span></div>
  <div class="lang-switch"><span class="lang-flag" role="img" aria-label="English flag"></span>English
    <svg width="10" height="7" viewBox="0 0 10 7"><path d="M1 1l4 4 4-4" fill="none" stroke="#fff" stroke-width="1.6"/></svg>
  </div>
  <div class="btn-book">Book Now</div>
</header>
<nav class="main-nav">
  <ul>
    <li class="is-current" style="width:146px">HOME</li>
    <li style="width:152px">TOURS</li>
    <li style="width:173px">CONTACT</li>
    <li style="width:152px">ABOUT</li>
  </ul>
</nav>
<section class="hero">
  <div class="hero-photo" role="img" aria-label="Group of smiling students standing by a river with a steel bridge behind"></div>
  <svg class="hero-arrow" style="left:106px" viewBox="0 0 20 30"><path d="M16 2L4 15l12 13" fill="none" stroke="#fff" stroke-width="3"/></svg>
  <svg class="hero-arrow" style="left:1075px" viewBox="0 0 20 30"><path d="M4 2l12 13L4 28" fill="none" stroke="#fff" stroke-width="3"/></svg>
  <div class="hero-caption">EDUCATIONAL SAFE. CULTURALLY BRIGHT WATTLE JOURNEYS ENLIGHTENING AND FUN</div>
</section>
<section class="features">
  <div class="feature" style="left:178px">
    <div class="feature-ring navy"><div class="feature-photo" role="img" aria-label="Students holding books" style="background:linear-gradient(160deg,#d9d4cc,#8a7f78)"></div></div>
    <div class="feature-title navy">Educational And Cultural</div>
  </div>
  <div class="feature" style="left:478px">
    <div class="feature-ring"><div class="feature-photo" role="img" aria-label="Happy students giving thumbs up" style="background:linear-gradient(160deg,#b7c4d4,#6e7f9b)"></div></div>
    <div class="feature-title">Safe And Secure</div>
  </div>
  <div class="feature" style="left:778px">
    <div class="feature-ring"><div class="feature-photo" role="img" aria-label="Aerial view of a harbour opera house" style="background:linear-gradient(160deg,#2d5b5e,#163a40)"></div></div>
    <div class="feature-title">Travel insurance</div>
  </div>
</section>
<section class="lower">
  <div class="rule"></div>
  <h2 class="about-title"><span class="gold">ABOUT</span> BRIGHT <span class="gold">WATTLE</span> JOURNEYS</h2>
  <svg class="title-ornament" viewBox="0 0 640 18">
    <line x1="0" y1="9" x2="302" y2="9" stroke="#cfcfcf"/>
    <line x1="338" y1="9" x2="640" y2="9" stroke="#cfcfcf"/>
    <circle cx="317" cy="9" r="8" fill="#2f3f85"/>
    <circle cx="317" cy="9" r="4.5" fill="#f5b31b"/>
  </svg>
  <p class="about-lead">At Bright Wattle Journeys We Are Passionate About Educational Travel And Opportunities For Students To Gain Academic And Cultural Understanding Of Australia.</p>
  <p class="about-body">14 day premium cultural and educational tours to Australian cities. Educational, safe, culturally enlightening and fun. Learn about educational institutions, history, sports, laws and customs, food and culture while improving your English.</p>
  <div class="btn-more">READ MORE</div>
</section>
<footer class="site-footer">
  <p class="copyright">© 2015&nbsp; BRIGHT WATTLE JOURNEYS. All Rights Reserved.</p>
  <div class="social"><span></span><span></span><span></span></div>
</footer>
</body>
</html>
```